Fresh, modern, fun business card for pediatric dental practice

Need a business card for fresh, modern, fun pediatric dental practice

Clean look that matches our website's font and colors

We prefer the look of curved corners on business cards

Target Market(s)

parents (mothers) of young children, professionals, mid-high class

Industry/Entity Type

Dental

Contact Information for Business Card

Maplebrook Pediatric Dentistry
482 Quarry Lane
Suite 517
Fernwood, PA 17299
717.555.0193
www.maplebrookkidsdental.example

Mei-Ran Tsai, DMD
Corinne Walbeck, DMD
(we are working on our email address, but we would like that on the card as well)

Font styles to use
Sans Serif

Requirements
Must have
• All info; we would also like to make cards for individual staff members
• colors from our website and color palatte, attatched
• use same font and design as website for branding
Nice to have
• clean, simple card that has a pop of color
• we would like to see a few designs with our tag line "where smiles get brighter"
• we are not sure if we want to have it on there or not
• we would like to see a few designs incorporating the ribbon graphic on our website where the word WELCOME is

```html
<!DOCTYPE html>
<html lang="en">
<head>
<meta charset="utf-8">
<title>Maplebrook Pediatric Dentistry – Business Card</title>
<link rel="stylesheet" href="https://fonts.googleapis.com/css2?family=Open+Sans:wght@400;600;700&display=swap">
<style>
  :root {
    --backdrop: #3b3431;
    --card-black: #1f1f1f;
    --card-white: #ffffff;
    --sun-gold: #f6b21b;
    --ink: #2a2a2a;
    --card-radius: 14px;
  }
  * { margin: 0; padding: 0; box-sizing: border-box; }
  html, body {
    width: 1200px;
    height: 715px;
    overflow: hidden;
    background: var(--backdrop);
    font-family: "Open Sans", Arial, sans-serif;
  }
  .sheet {
    position: relative;
    width: 1200px;
    height: 715px;
  }
  .card {
    position: absolute;
    top: 207px;
    width: 520px;
    height: 300px;
    border-radius: var(--card-radius);
    overflow: hidden;
    box-shadow: 0 12px 30px rgba(0,0,0,0.35);
  }
  .card--back {
    left: 50px;
    background: var(--card-black);
    display: flex;
    align-items: center;
    justify-content: center;
  }
  .card--front {
    left: 630px;
    background: var(--card-white);
  }
  .wordmark {
    display: flex;
    align-items: center;
    gap: 12px;
    color: var(--sun-gold);
    font-weight: 700;
    line-height: 1.05;
  }
  .wordmark__dot {
    flex: none;
    border-radius: 50%;
    border: 3px solid var(--sun-gold);
  }
  .card--back .wordmark { font-size: 30px; }
  .card--back .wordmark__dot { width: 34px; height: 34px; }
  .front-art {
    position: absolute;
    inset: 0;
    width: 100%;
    height: 100%;
  }
  .front-brand {
    position: absolute;
    right: 26px;
    top: 112px;
    width: 210px;
  }
  .front-brand .wordmark { font-size: 22px; }
  .front-brand .wordmark__dot { width: 26px; height: 26px; }
  .contact {
    position: absolute;
    left: 30px;
    top: 92px;
    color: var(--ink);
    font-size: 11.5px;
    line-height: 1.55;
  }
  .contact__name {
    color: var(--sun-gold);
    font-size: 17px;
    font-weight: 700;
    letter-spacing: 0.5px;
    line-height: 1.2;
  }
  .contact__title {
    font-size: 11px;
    margin-bottom: 8px;
  }
  .contact__line {
    display: flex;
    align-items: center;
    gap: 6px;
  }
  .contact__icon {
    width: 10px;
    height: 10px;
    flex: none;
    fill: var(--sun-gold);
  }
</style>
</head>
<body>
<main class="sheet">
  <section class="card card--back" aria-label="Card back">
    <div class="wordmark">
      <span class="wordmark__dot"></span>
      <span>Maplebrook<br>Pediatric Dentistry</span>
    </div>
  </section>

  <section class="card card--front" aria-label="Card front">
    <svg class="front-art" viewBox="0 0 520 300" aria-hidden="true">
      <path d="M268 0 C210 70 214 200 430 300 L520 300 L520 0 Z" fill="var(--card-black)"/>
      <path d="M258 0 C198 72 204 202 418 300" fill="none" stroke="var(--sun-gold)" stroke-width="6"/>
    </svg>

    <div class="contact">
      <p class="contact__name">CORINNE WALBECK</p>
      <p class="contact__title">DMD</p>
      <p>482 Quarry Lane</p>
      <p>Suite 517 Fernwood, PA 17299</p>
      <p class="contact__line">
        <svg class="contact__icon" viewBox="0 0 10 10"><path d="M2 0 L4 2.5 L3 3.8 Q4.5 6 6.2 7 L7.5 6 L10 8 L8.5 10 Q3 9 0 2 Z"/></svg>
        717.555.0193
      </p>
      <p class="contact__line">
        <svg class="contact__icon" viewBox="0 0 10 10"><rect x="0" y="2" width="10" height="6.5" rx="1"/></svg>
        hello@maplebrookkids.example
      </p>
      <p class="contact__line">
        <svg class="contact__icon" viewBox="0 0 10 10"><circle cx="5" cy="5" r="5"/></svg>
        www.maplebrookkidsdental.example
      </p>
    </div>

    <div class="front-brand">
      <div class="wordmark">
        <span class="wordmark__dot"></span>
        <span>Maplebrook<br>Pediatric Dentistry</span>
      </div>
    </div>
  </section>
</main>
</body>
</html>
```